Velvet Glow Co. Derma Roller packaging design

I need a box designed for a skin care brand called Velvet Glow Co. The box will be for our Derma Roller- a skin rejuvenation device. It will be sold online with lots of competition. I would like a modern, high end design, something that stands out and looks amazing. My logo is blush pink and black, for packaging i need no more than 3 colours, maybe gold if any other colour is used. A photo of a sample derma roller is attached below for an idea of what the product looks like, however my roller with have a clear handle with a black roller. The roller comes in a clear case, the box dimensions will need to be 16 cm long, 4 cm high, 4.5 cm wide.
ATTACHED ARE 2 SAMPLE BOXES AS AN EXAMPLE OF THE SIZE OF BOX REQUIRED!

Target Market(s)

25-50 year old women in the US

Colors
e667a6
000000
efefef

Requirements
Must have
• LOGO
• NAME OF PRODUCT- Cosmetic Derma Roller
• NEEDLE DEPTH- 0.25mm
• CAUTION- For personal use only, Do not use if allergic to metal, Do not use on open skin, wounds or active acne, sterilise roller before and after use.
Nice to have
• BENEFITS- Skin Rejuvenation, Collagen Induction Therapy, Increase product absorption, reduce acne scars and pigmentation
• FEATURES- 540 high quality titanium needles, ultra sharp needle tips, cross-line needle arrangement, ergonomic handle, anti slip grip,

```html
<!DOCTYPE html>
<html lang="en">
<head>
<meta charset="utf-8">
<title>Velvet Glow Co. – Cosmetic Derma Roller Packaging</title>
<link rel="stylesheet" href="https://fonts.googleapis.com/css2?family=Oswald:wght@400;500&display=swap">
<style>
  :root {
    --page-bg: #f8f2f0;
    --floral-light: #ece6e7;
    --floral-brown: #5b3b2d;
    --floral-pink: #e9998b;
    --label-bg: #fdf8f5;
    --rose-gold: #d69c86;
    --rose-gold-light: #efc7b6;
    --ink: #1d1a19;
  }
  * { box-sizing: border-box; margin: 0; padding: 0; }
  html, body { width: 1200px; height: 1200px; overflow: hidden; }
  body {
    background: radial-gradient(circle at 50% 50%, #fffdfc 0%, var(--page-bg) 100%);
    font-family: "Oswald", sans-serif;
    position: relative;
  }
  .box-panel {
    position: absolute;
    left: 48px;
    width: 1104px;
    height: 356px;
    box-shadow: 0 3px 8px rgba(60, 40, 30, 0.25);
    overflow: hidden;
  }
  .box-panel--front { top: 182px; }
  .box-panel--back { top: 662px; }
  .floral-pattern {
    position: absolute;
    inset: 0;
    background:
      radial-gradient(circle at 14% 30%, var(--floral-pink) 0 6%, transparent 12%),
      radial-gradient(circle at 86% 38%, var(--floral-pink) 0 5%, transparent 11%),
      radial-gradient(circle at 10% 85%, var(--floral-brown) 0 8%, transparent 16%),
      radial-gradient(circle at 92% 15%, var(--floral-brown) 0 6%, transparent 14%),
      radial-gradient(circle at 60% 100%, var(--floral-brown) 0 10%, transparent 20%),
      radial-gradient(circle at 45% 0%, var(--floral-brown) 0 8%, transparent 18%),
      var(--floral-light);
  }
  .label {
    position: absolute;
    background: var(--label-bg);
    text-align: center;
  }
  .label--front {
    left: 386px;
    top: 40px;
    width: 332px;
    height: 280px;
    border: 3px solid var(--rose-gold);
  }
  .label--back {
    left: 248px;
    top: 58px;
    width: 608px;
    height: 238px;
    padding: 22px 28px 0;
    text-align: left;
  }
  .brand-name {
    position: absolute;
    left: 0; right: 0;
    top: 96px;
    font-weight: 400;
    font-size: 34px;
    letter-spacing: 3px;
    color: var(--ink);
    text-transform: uppercase;
  }
  .product-title {
    font-weight: 500;
    font-size: 30px;
    letter-spacing: 0.5px;
    color: var(--rose-gold);
    background: linear-gradient(90deg, var(--rose-gold-light), var(--rose-gold) 55%, #c98a74);
    -webkit-background-clip: text;
    background-clip: text;
    -webkit-text-fill-color: transparent;
    line-height: 1;
  }
  .label--front .product-title {
    position: absolute;
    left: 0; right: 0;
    top: 222px;
  }
  .label--back .product-title {
    text-align: center;
    margin-bottom: 17px;
  }
  .spec {
    font-weight: 400;
    font-size: 13.4px;
    line-height: 18px;
    color: var(--ink);
    text-transform: uppercase;
    margin-bottom: 18px;
  }
</style>
</head>
<body>

  <section class="box-panel box-panel--front">
    <div class="floral-pattern" role="img" aria-label="Engraved floral pattern with blush pink blossoms, brown leaves and grey acanthus scrolls"></div>
    <div class="label label--front">
      <p class="brand-name">Velvet Glow Co.</p>
      <h1 class="product-title">COSMETIC DERMA ROLLER</h1>
    </div>
  </section>

  <section class="box-panel box-panel--back">
    <div class="floral-pattern" role="img" aria-label="Engraved floral pattern with blush pink blossoms, brown leaves and grey acanthus scrolls"></div>
    <div class="label label--back">
      <h2 class="product-title">COSMETIC DERMA ROLLER</h2>
      <p class="spec">Benefits: Skin rejuvenation, collagen induction therapy, increase product absorption, reduce acne scars and pigmentation</p>
      <p class="spec">Features: 540 high quality 0.25 mm titanium needles, ultra sharp needle tips, cross-line needle arrangement, ergonomic handle, anti slip grip</p>
      <p class="spec">Caution: For personal use only, do not use if allergic to metal, do not use on open skin, wounds or active acne, sterilise roller before and after use.</p>
    </div>
  </section>

</body>
</html>
```